Membership Drive "End of Spring Sale"

Looking to run a Direct Debit Sale for November 2019 to boost membership number up. This is our slowest area for membership growth, many choose not to do direct debit, special is designed to increase numbers. Artwork will be display via social media (QP and Pictoria) as well as in store. Artwork must be eye catching and direct to the customer. Customer should feel a sense of relief with monthly payments instead of one large payment.

Heading: "End of Spring Special"
Direct Debit
$39.95 per month
Terms and conditions apply"
*Offer End 30th November

Slogan:
"More Energy
More Atmosphere
Feel the Difference
Make the change now" can be placed where suits.

below are other promos we had designed on Sketch Harbor along with potential photos to be included into this promo

Target Market(s)

Males and Females aged between 18 - 40

Industry/Entity Type

Fitness

Colors

Designer to choose colors to be used in the design.

Requirements
Must have
• Must emphasize "End of Spring Special" $39.95 per month and
• under neath strict terms and conditions apply
• Offer Ends 30th of November
• "All of our contact details"
• Address: 14 Penrose Rd Marlow Heights 3187
• Ph: 9471 2856
• www.brambleforge.com.au
• Design format must come in poster size A0 size, Pictoria format, Facebook cover and 800 x 800 for the website
Nice to have
• With the photos attached at least one female and one male in the overall design. Lots of color in relation to Spring and artistic effects to catch peoples eyes.
• Also to include "Celebrating 49 years"

```html
<!DOCTYPE html>
<html lang="en">
<head>
<meta charset="utf-8">
<title>Bramble Forge – End of Spring Special</title>
<link rel="stylesheet" href="https://fonts.googleapis.com/css2?family=Montserrat:ital,wght@0,500;0,600;0,700;0,800;1,600;1,700&family=Sacramento&display=swap">
<style>
  :root {
    --page-bg: #d9dadc;
    --teal-deep: #10302f;
    --teal-mid: #1f5550;
    --teal-bright: #5fc4a8;
    --skin-warm: #8a5a44;
    --gold: #f2c81b;
    --white: #ffffff;
    --soft-white: #e9eeee;
  }
  * { box-sizing: border-box; margin: 0; padding: 0; }
  html, body {
    width: 1200px; height: 800px; overflow: hidden;
    background: var(--page-bg);
    font-family: "Montserrat", Arial, sans-serif;
  }
  .poster {
    position: absolute; left: 330px; top: 20px;
    width: 540px; height: 760px; overflow: hidden;
    background: linear-gradient(160deg, var(--teal-deep) 0%, #17403d 55%, var(--teal-deep) 100%);
  }
  .hero-photo {
    position: absolute; left: 0; top: 40px; width: 540px; height: 560px;
    background:
      radial-gradient(ellipse 38% 30% at 62% 42%, rgba(138,90,68,.85), rgba(138,90,68,0) 70%),
      radial-gradient(ellipse 30% 22% at 75% 22%, rgba(120,80,60,.8), rgba(120,80,60,0) 70%),
      radial-gradient(ellipse 60% 45% at 60% 30%, var(--teal-bright), rgba(95,196,168,0) 75%),
      linear-gradient(175deg, rgba(31,85,80,.9), rgba(16,48,47,.2));
  }
  .brand-name {
    position: absolute; left: 58px; top: 36px;
    font-weight: 800; font-size: 26px; line-height: 1; letter-spacing: .5px;
    color: var(--gold); text-transform: uppercase;
  }
  .headline { position: absolute; left: 0; width: 540px; }
  .headline-script {
    position: absolute; left: 168px; top: 170px;
    font-family: "Sacramento", cursive; font-size: 104px; line-height: 1;
    color: var(--gold); transform: rotate(-8deg);
  }
  .headline-main {
    position: absolute; left: 148px; top: 260px;
    font-weight: 800; font-size: 62px; line-height: 58px; color: var(--white);
    text-align: center; width: 264px;
  }
  .anniversary {
    position: absolute; left: 58px; top: 390px;
    font-weight: 800; font-size: 29px; line-height: 1; color: var(--gold); letter-spacing: .3px;
  }
  .divider {
    position: absolute; left: 58px; top: 433px; width: 427px; height: 3px; background: var(--white);
  }
  .price {
    position: absolute; left: 58px; top: 448px;
    font-weight: 700; font-size: 40px; line-height: 1; color: var(--white);
  }
  .terms {
    position: absolute; left: 58px; top: 500px;
    font-weight: 500; font-size: 10.5px; color: var(--soft-white); text-transform: uppercase;
  }
  .slogan {
    position: absolute; right: 55px; top: 553px; text-align: right;
    font-weight: 600; font-size: 16.5px; line-height: 23px; color: var(--white);
  }
  .slogan em { font-style: italic; font-weight: 700; }
  .call-to-action {
    position: absolute; right: 55px; top: 628px;
    font-weight: 600; font-size: 25px; line-height: 1; color: var(--white);
  }
  .cta-underline { position: absolute; left: 120px; top: 660px; }
  .website {
    position: absolute; right: 55px; top: 694px;
    font-weight: 700; font-size: 15.5px; color: var(--gold);
  }
  .contact-row {
    position: absolute; right: 55px; top: 727px;
    display: flex; gap: 16px; align-items: center;
    font-weight: 600; font-size: 13.5px; color: var(--white);
  }
  .contact-item { display: flex; align-items: center; gap: 6px; }
</style>
</head>
<body>
  <main class="poster">
    <div class="hero-photo" role="img" aria-label="Photograph of a muscular man in a black tank top pulling down a cable bar, over teal painted brush strokes"></div>

    <div class="brand-name">Bramble Forge</div>

    <h1 class="headline">
      <span class="headline-script">End of</span>
      <span class="headline-main">SPRING<br>SPECIAL</span>
    </h1>

    <p class="anniversary">CELEBRATING 49 YEARS</p>
    <div class="divider"></div>
    <p class="price">$39.95/PER MONTH</p>
    <p class="terms">*Terms and conditions apply - offer end 30th of November</p>

    <p class="slogan">MORE <em>ENERGY</em><br>MORE <em>ATMOSPHERE</em><br><em>FEEL THE DIFFERENCE</em></p>

    <p class="call-to-action">MAKE THE CHANGE NOW</p>
    <svg class="cta-underline" width="368" height="10" viewBox="0 0 368 10" aria-hidden="true">
      <path d="M4 6 C 90 3, 250 3, 364 5" stroke="#f2c81b" stroke-width="7" stroke-linecap="round" fill="none"/>
    </svg>

    <p class="website">WWW.BRAMBLEFORGE.COM.AU</p>

    <div class="contact-row">
      <span class="contact-item">
        <svg width="10" height="14" viewBox="0 0 10 14" aria-hidden="true">
          <path d="M5 0a5 5 0 0 0-5 5c0 3.8 5 9 5 9s5-5.2 5-9a5 5 0 0 0-5-5zm0 7a2 2 0 1 1 0-4 2 2 0 0 1 0 4z" fill="#ffffff"/>
        </svg>
        14 PENROSE RD MARLOW HEIGHTS 3187
      </span>
      <span class="contact-item">
        <svg width="13" height="13" viewBox="0 0 24 24" aria-hidden="true">
          <path d="M6.6 10.8a15.1 15.1 0 0 0 6.6 6.6l2.2-2.2a1 1 0 0 1 1-.25 11.4 11.4 0 0 0 3.6.57 1 1 0 0 1 1 1V20a1 1 0 0 1-1 1A17 17 0 0 1 3 4a1 1 0 0 1 1-1h3.5a1 1 0 0 1 1 1c0 1.25.2 2.45.57 3.6a1 1 0 0 1-.25 1z" fill="#ffffff"/>
        </svg>
        9471 2856
      </span>
    </div>
  </main>
</body>
</html>
```